Business Cards Design for the electrical wholesaler: clean bold dynamic :)

We need a business card design that would follow our latest brand guidelines. As an electrical wholesaler we want to bring a fresh look and feel into the industry. The design should be clean bold and dynamic. It should come alive with the renewed energy of our green colour. Our grey colour should keep things balanced and complement the notion of maturity and responsibility. We employ Lato as a corporate font however are not bound by this font and we’re open to interpretation here.

Target Market(s)

Electrical contractors

Industry/Entity Type

Business

Contact Information for Business Card

Logo
Name & Surname: Halyna Dorosh
Job Title: Director of Marketing
Email: halya.dorosh@quillmail.example
Cell phone: XXX.XXX.XXXX
Address: 20517 - 87 Ave. Edmonton, AB, Canada. T6K 4N8
Business Phone: 780.555.0184
Website: www.brovix.example

Font styles to use
Other font styles liked:
• Lato

Requirements
Must have
• Logo & website
Nice to have
• Brand elements - some of them you may find in the attached Brand Guidelines (e.g. three lines on the background signifying "W")

```html
<!DOCTYPE html>
<html lang="en">
<head>
<meta charset="utf-8">
<title>Brovix Business Card</title>
<link rel="stylesheet" href="https://fonts.googleapis.com/css2?family=Lato:wght@400;700;900&display=swap">
<style>
  :root {
    --backdrop: #3a3a3b;
    --card-black: #1c1c1d;
    --card-band: #4a4c4f;
    --brand-green: #7dc12a;
    --ink-white: #f1f1f1;
    --ink-muted: #2e2f31;
    --ink-emboss: #3b3b3d;
  }
  * { margin: 0; padding: 0; box-sizing: border-box; }
  html, body { width: 799px; height: 1200px; overflow: hidden; }
  body {
    background: var(--backdrop);
    font-family: "Lato", sans-serif;
    display: flex;
    flex-direction: column;
    align-items: center;
    justify-content: space-around;
    padding: 60px 0;
  }
  .card {
    position: relative;
    width: 580px;
    height: 340px;
    border-radius: 22px;
    background: var(--card-black);
    overflow: hidden;
  }
  .card-front { display: flex; align-items: center; justify-content: center; }
  .wordmark {
    display: flex;
    align-items: center;
    gap: 14px;
    font-weight: 900;
    letter-spacing: 1px;
  }
  .wordmark .mark-square { width: 0.7em; height: 0.7em; background: currentColor; }
  .card-front .wordmark { font-size: 78px; color: var(--ink-emboss); }

  .card-back .wordmark {
    position: absolute; top: 30px; left: 36px;
    font-size: 50px; color: var(--ink-white);
  }
  .card-back .wordmark .mark-square { background: var(--brand-green); }
  .info-band {
    position: absolute; left: 0; right: 0; top: 112px; height: 160px;
    background: var(--card-band);
  }
  .person { position: absolute; top: 128px; left: 36px; }
  .person-name { font-size: 30px; font-weight: 700; color: var(--brand-green); }
  .person-title { font-size: 16px; color: var(--ink-white); margin-top: 2px; }
  .contacts {
    position: absolute; top: 200px; left: 36px;
    list-style: none; font-size: 15px; color: var(--ink-white);
  }
  .contacts li { display: flex; align-items: center; gap: 10px; margin-bottom: 8px; }
  .contacts .row { display: flex; gap: 22px; }
  .contacts .row span { display: flex; align-items: center; gap: 10px; }
  .contact-icon { width: 14px; height: 14px; flex: none; }
  .web-accent { color: var(--brand-green); }
  .address {
    position: absolute; left: 36px; bottom: 28px;
    font-size: 15px; color: var(--ink-muted); font-weight: 700;
  }
</style>
</head>
<body>
  <section class="card card-front" aria-label="Card front">
    <div class="wordmark"><span class="mark-square"></span>Brovix</div>
  </section>

  <section class="card card-back" aria-label="Card back">
    <div class="wordmark"><span class="mark-square"></span>Brovix</div>
    <div class="info-band"></div>
    <div class="person">
      <p class="person-name">Halyna Dorosh</p>
      <p class="person-title">Founder &amp; CEO</p>
    </div>
    <ul class="contacts">
      <li>
        <svg class="contact-icon" viewBox="0 0 14 14"><circle cx="7" cy="7" r="7" fill="#7dc12a"/><path d="M4.5 3.5h1.6l.7 2-1 .8a5 5 0 0 0 2.4 2.4l.8-1 2 .7v1.6c0 .5-.4.8-.9.8A6.5 6.5 0 0 1 3.7 4.4c0-.5.3-.9.8-.9z" fill="#1c1c1d"/></svg>
        +1 780-555-0184
      </li>
      <li class="row">
        <span>
          <svg class="contact-icon" viewBox="0 0 14 14"><circle cx="7" cy="7" r="7" fill="#7dc12a"/><rect x="3.5" y="4.5" width="7" height="5" fill="none" stroke="#1c1c1d" stroke-width="1"/><path d="M3.5 4.5 7 7.3l3.5-2.8" fill="none" stroke="#1c1c1d" stroke-width="1"/></svg>
          halya.dorosh@quillmail.example
        </span>
      </li>
      <li>
        <svg class="contact-icon" viewBox="0 0 14 14"><circle cx="7" cy="7" r="7" fill="#7dc12a"/><circle cx="7" cy="7" r="3.5" fill="none" stroke="#1c1c1d" stroke-width="1"/><path d="M3.5 7h7M7 3.5c-1.5 2-1.5 5 0 7M7 3.5c1.5 2 1.5 5 0 7" fill="none" stroke="#1c1c1d" stroke-width=".8"/></svg>
        www.<span class="web-accent">brovix</span>.example
      </li>
    </ul>
    <p class="address">20517 - 87 Ave. Edmonton, AB, Canada. T6K 4N8</p>
  </section>
</body>
</html>
```